KORV PTY LTD - Business Cards

Design a modern business card - using the attached Designs.
Same design as on the front, apart from the names/numbers/emails to be different.
We want the cards to be very glossy to stand out, do I think the simple black/white/metallic will be effective.
Both lots of details below:

Tom Wrenshaw
Director
tom_korv@nulvane.com
0438 274 093

Lewis Corbyn
Director
lewis_korv@nulvane.com
0419 385 642

Industry/Entity Type

Business

```html
<!DOCTYPE html>
<html lang="en">
<head>
<meta charset="utf-8">
<title>KORV PTY LTD – Business Cards</title>
<link href="https://fonts.googleapis.com/css2?family=Michroma&family=Open+Sans:wght@600&display=swap" rel="stylesheet">
<style>
  :root {
    --backdrop: #e9e9eb;
    --card-dark: #1f2023;
    --card-mid: #4a4c51;
    --card-light: #8d9096;
    --sheen: rgba(255,255,255,0.28);
    --silver: #f1f2f4;
    --silver-muted: #c9cbcf;
    --badge-ring: #5b5e63;
  }
  html, body {
    margin: 0;
    width: 1200px;
    height: 913px;
    overflow: hidden;
    background: var(--backdrop);
  }
  .canvas {
    position: relative;
    width: 1200px;
    height: 913px;
  }
  .business-card {
    position: absolute;
    width: 540px;
    height: 309px;
    border-radius: 4px;
    overflow: hidden;
    box-shadow: 0 10px 28px rgba(0,0,0,0.28);
    background:
      linear-gradient(115deg, transparent 30%, var(--sheen) 44%, transparent 58%),
      radial-gradient(ellipse at 50% 35%, var(--card-light) 0%, var(--card-mid) 45%, var(--card-dark) 100%);
    color: var(--silver);
    text-align: center;
  }
  .business-card--primary { left: 50px; top: 150px; }
  .business-card--secondary { left: 610px; top: 450px; }

  .card-texture {
    position: absolute;
    inset: 0;
    background: linear-gradient(180deg, rgba(255,255,255,0.06), rgba(0,0,0,0.12));
  }
  .brand-mark {
    position: absolute;
    left: 50%;
    top: 30px;
    transform: translateX(-50%);
    display: flex;
    align-items: center;
    gap: 16px;
    white-space: nowrap;
  }
  .brand-mark__circle {
    width: 46px;
    height: 46px;
    border-radius: 50%;
    background: var(--badge-ring);
  }
  .brand-mark__name {
    font-family: "Michroma", sans-serif;
    font-size: 40px;
    color: var(--silver);
    letter-spacing: 4px;
  }
  .card-holder {
    position: absolute;
    left: 0;
    right: 0;
    top: 150px;
  }
  .card-holder__name {
    font-family: "Michroma", sans-serif;
    font-size: 28px;
    font-weight: 400;
    letter-spacing: 2px;
    text-transform: uppercase;
    margin: 0;
    color: var(--silver);
    white-space: nowrap;
  }
  .card-holder__role {
    font-family: "Open Sans", sans-serif;
    font-weight: 600;
    font-size: 11px;
    letter-spacing: 2px;
    text-transform: uppercase;
    color: var(--silver-muted);
    margin: 4px 0 0;
  }
  .card-holder__contact {
    font-family: "Open Sans", sans-serif;
    font-weight: 600;
    font-size: 15px;
    color: var(--silver);
    margin: 30px 0 0;
    white-space: nowrap;
  }
</style>
</head>
<body>
<main class="canvas">

  <article class="business-card business-card--primary">
    <div class="card-texture" role="img" aria-label="Fine metallic diamond texture"></div>
    <div class="brand-mark">
      <span class="brand-mark__circle"></span>
      <span class="brand-mark__name">KORV</span>
    </div>
    <div class="card-holder">
      <h2 class="card-holder__name">Tom Wrenshaw</h2>
      <p class="card-holder__role">Director</p>
      <p class="card-holder__contact">Ph.: 0438 274 093 • Email: tom_korv@nulvane.com</p>
    </div>
  </article>

  <article class="business-card business-card--secondary">
    <div class="card-texture" role="img" aria-label="Fine metallic diamond texture"></div>
    <div class="brand-mark">
      <span class="brand-mark__circle"></span>
      <span class="brand-mark__name">KORV</span>
    </div>
    <div class="card-holder">
      <h2 class="card-holder__name">Lewis Corbyn</h2>
      <p class="card-holder__role">Director</p>
      <p class="card-holder__contact">Ph.: 0419 385 642 • Email: lewis_korv@nulvane.com</p>
    </div>
  </article>

</main>
</body>
</html>
```